IT Company Business Card Design w/Stationary Design

We have a great logo we like! We are looking to redesign our business cards and all company logo'd merchandise/materials.

We are an IT Company located near the Bay Area (San Francisco, CA). We specialize in Managed Services and offer complete IT Computer and Network Support to Businesses of all sizes. We thrive on making a lasting impression. We have been doing IT for 15yrs+ but are young at heart. We like to stand out and be different. We want to be unique and have a recognizable brand. We need our logo to represent who we are. We are young, professional, creative and outstanding. We don't want to blend in, we want to stand out. Our business card needs to stand out and grab attention. Something Bold, yet simple and clean. (I will provide ideas of what we like to give a taste of what we are looking for).

The design can include any kind of texture/artistic design or sizing EXCEPT please "no square card designs" as they don't seem to fit in wallets very well. We dont mind curved edges, rounded corners, vertical layouts or horizontal layouts, embossing, letter press or raised surfaces. Again, we dont want to look average or plain or boring. :) Be creative - yet practical! We have ordered from ZEPLA designs before and been very happy. Their card sizes tend to be a little different, so beware. Hope this helps!

Target Market(s)

Businesses - Small to Medium, Corporations, Publicly Traded Companies

Industry/Entity Type

Business

Contact Information for Business Card

Harbor Lantern IT
7158 Delacroix Avenue
Suite K
Brellwood, CA 95871

Office 209.555.0173
Direct 209.555.0148
Cell 209.555.0196

Dale Pruitt
Founder, CEO
www.hlxq.com
dpruitt@hlxq.com

Locations Serviced: Brellwood, Tamsford, Orvale Heights, Quillan (incorporate this on the card ONLY if there's a good place to do so).

What we specialize in: Computer, Network, Voice, Data. (IT Services)

Our Logo Colors: Black and Blue (#006699). Open to using grey or orange as well - but not required. Don't want too busy....

Logo Font: "Cinthe" (Will attach logo font). We want type style to be clean. You can show different font types including our logo font - and we are open to other font ideas.

The logo can be separated. You can use elements together or apart. Surprise us! :) We "REALLY" want the "hl" to be our identifier/our brand people recognize.

Font styles to use
Sans Serif

Colors
0355a3
3176b5
f37122
f78f20
faa54b
474747
aaaaaa
757575
000000

Requirements
Must have
• Bold, Big, Colorful, Modern/yet Fun, Clean Design, Stand Out Presence, Texture would be welcomed - but not necessary, Card design shape can include cut corners or rounded or square edges. Be creative. (HOWEVER, we don't want a square design because we have found it doesn't fit in wallets that easily).
• We do like using ZEPLA printing company (Which they have particular sizing on their card templates - beware), but are open to other design templates/printing companies as well. We just want to make sure its easy to find a print company to do our work. Too unique could be costly and hard to get cards printed.
• Colors to use: Our logo Blue (#006699), with either whites, grays, black, shades of our blue, and maybe a pinch of orange if needed. Primarily, blue, white, gray or black.
Nice to have
• Texture would be cool or little different edging or shape - but nothing too costly to print. I have seen cards with 3 sharp edges and one round edge. Something like that would be cool as an option. Or a vertical card.
• I love a faded watermark look. It would be nice to see some shading of our circle logo on a few designs. The circle with "hl" in it OR.... taking just the "hl" and using it alone.
Should not have
• No square card designs. Nothing too expensive or elaborate to print. No busy fonts. Do not like Times New Roman type fonts (too old looking). Not a lot of orange (if you even choose to use some orange).

```html
<!DOCTYPE html>
<html lang="en">
<head>
<meta charset="utf-8">
<title>Harbor Lantern IT — Business Card</title>
<link rel="stylesheet" href="https://fonts.googleapis.com/css2?family=Open+Sans:wght@400;600&display=swap">
<style>
  :root {
    --page: #e8ebee;
    --blue-light: #2aa3da;
    --blue: #1a8cc6;
    --blue-deep: #136fa5;
    --white: #ffffff;
    --white-soft: rgba(255,255,255,0.88);
    --rule: rgba(255,255,255,0.75);
    --shadow: rgba(20,50,80,0.18);
  }
  * { margin: 0; padding: 0; box-sizing: border-box; }
  html, body { width: 1200px; height: 1023px; overflow: hidden; }
  body {
    background: var(--page);
    font-family: "Open Sans", Arial, sans-serif;
    position: relative;
  }
  .card {
    position: absolute;
    left: 215px;
    width: 770px;
    height: 440px;
    border-radius: 30px;
    overflow: hidden;
    box-shadow: 0 10px 28px var(--shadow);
  }
  .card-front { top: 36px; }
  .card-back { top: 540px; }

  .pattern-field {
    position: absolute; inset: 0;
    background:
      radial-gradient(ellipse at 70% 30%, rgba(255,255,255,0.14), transparent 60%),
      linear-gradient(135deg, var(--blue-light) 0%, var(--blue) 50%, var(--blue-deep) 100%);
  }
  .card-shapes { position: absolute; inset: 0; }

  .brand-mark {
    position: absolute;
    left: 196px; top: 176px;
    font-size: 64px; font-weight: 600;
    color: var(--blue);
    line-height: 1;
  }

  .contact { position: absolute; color: var(--white); }
  .contact-name {
    left: 350px; top: 40px;
    font-size: 26px; font-weight: 600;
    white-space: nowrap;
  }
  .contact-name .title { font-weight: 400; font-size: 20px; }
  .name-rule {
    position: absolute; left: 350px; top: 86px;
    width: 390px; height: 1.5px; background: var(--rule);
  }
  .contact-list { left: 342px; top: 104px; list-style: none; }
  .contact-list li {
    display: flex; align-items: center; gap: 14px;
    height: 34px; font-size: 17px; color: var(--white-soft);
    white-space: nowrap;
  }
  .contact-list svg { width: 22px; height: 22px; flex: none; }
  .address {
    position: absolute; left: 378px; top: 282px;
    font-size: 17px; line-height: 25px; color: var(--white-soft);
    white-space: nowrap;
  }
  .locations {
    position: absolute; left: 378px; top: 350px;
    font-size: 17px; line-height: 25px; color: var(--white-soft);
    white-space: nowrap;
  }
  .locations .label { font-weight: 600; color: var(--white); }
  .locations .cities { font-size: 15px; }

  .back-brand {
    position: absolute; left: 300px; top: 176px;
    display: flex; align-items: center; gap: 22px;
  }
  .back-brand .dot {
    width: 88px; height: 88px; border-radius: 50%;
    background: var(--white);
  }
  .back-brand .wordmark {
    font-size: 44px; font-weight: 600; color: var(--white);
    line-height: 1.05;
  }
  .web {
    position: absolute; left: 40px; bottom: 34px;
    font-size: 18px; color: var(--white-soft);
  }
</style>
</head>
<body>

<section class="card card-front" aria-label="Card front">
  <div class="pattern-field" role="img" aria-label="Faint repeating monogram pattern on blue"></div>
  <svg class="card-shapes" viewBox="0 0 770 440" aria-hidden="true">
    <path d="M0 0 H230 C360 120 360 320 230 440 H0 Z" fill="#ffffff"/>
    <circle cx="100" cy="220" r="76" fill="#1a8cc6"/>
  </svg>
  <div class="brand-mark">hl</div>

  <div class="contact contact-name">Dale Pruitt <span class="title">| Founder, CEO</span></div>
  <div class="name-rule"></div>

  <ul class="contact contact-list">
    <li>
      <svg viewBox="0 0 22 22"><circle cx="11" cy="11" r="10" fill="none" stroke="#fff" stroke-width="1.5"/><rect x="8" y="5.5" width="6" height="11" rx="1" fill="#fff"/></svg>
      209.555.0196
    </li>
    <li>
      <svg viewBox="0 0 22 22"><circle cx="11" cy="11" r="10" fill="none" stroke="#fff" stroke-width="1.5"/><rect x="6" y="7" width="10" height="8" rx="1.5" fill="#fff"/></svg>
      209.555.0173 (Office)
    </li>
    <li>
      <svg viewBox="0 0 22 22"><circle cx="11" cy="11" r="10" fill="none" stroke="#fff" stroke-width="1.5"/><path d="M7 6 L10 6 L10.5 9 L9 10 Q10.5 13 12.5 13.5 L13.5 12 L16 12.5 L16 15.5 Q9 16 6.5 8 Z" fill="#fff"/></svg>
      209.555.0148 (Direct)
    </li>
    <li>
      <svg viewBox="0 0 22 22"><circle cx="11" cy="11" r="10" fill="none" stroke="#fff" stroke-width="1.5"/><rect x="5.5" y="7" width="11" height="8" fill="#fff"/><path d="M5.5 7 L11 11.5 L16.5 7" fill="none" stroke="#1a8cc6" stroke-width="1.2"/></svg>
      dpruitt@hlxq.com
    </li>
    <li>
      <svg viewBox="0 0 22 22"><circle cx="11" cy="11" r="10" fill="none" stroke="#fff" stroke-width="1.5"/><path d="M11 17 C7 12 7 10 7 9 A4 4 0 0 1 15 9 C15 10 15 12 11 17 Z" fill="#fff"/><circle cx="11" cy="9" r="1.5" fill="#1a8cc6"/></svg>
      Harbor Lantern IT
    </li>
  </ul>

  <div class="address">7158 Delacroix Avenue Suite<br>K Brellwood, CA 95871</div>
  <div class="locations">
    <div class="label">Locations Serviced:</div>
    <div class="cities">Brellwood, Tamsford, Orvale Heights, Quillan</div>
  </div>
</section>

<section class="card card-back" aria-label="Card back">
  <div class="pattern-field" role="img" aria-label="Faint repeating monogram pattern on blue"></div>
  <div class="back-brand">
    <div class="dot"></div>
    <div class="wordmark">Harbor<br>Lantern</div>
  </div>
  <div class="web">www.hlxq.com</div>
</section>

</body>
</html>
```